Clear Cable Record Format Sticker

We need a set of stickers (~5-7cm) to promote the Clear Cable Record Format. Most of the people we will be handing these out to are technically minded (network operators, open-source coders, Internet standards folk, Internet measurement researchers). The design should include the CCRF icon and colour scheme (see here https://ccrf-sample.example/en/resources/).

network operators, open-source coders, Internet standards folk, Internet measurement researchers

• Hind

```html
<!DOCTYPE html>
<html lang="en">
<head>
<meta charset="utf-8">
<title>Clear Cable Record Format Sticker</title>
<link rel="stylesheet" href="https://fonts.googleapis.com/css2?family=Hind:wght@500;600&family=Montserrat:wght@700&display=swap">
<style>
  :root {
    --backdrop: #5e5e5e;
    --ring-blue: #1d80c7;
    --ring-white: #ffffff;
    --night: #14112b;
    --lime: #b5d334;
    --text-white: #ffffff;
  }
  html, body {
    margin: 0;
    padding: 0;
    overflow: hidden;
  }
  body {
    width: 1200px;
    height: 560px;
    background: var(--backdrop);
    display: flex;
    align-items: center;
    justify-content: center;
  }
  .sticker {
    width: 510px;
    height: 510px;
    display: block;
    filter: drop-shadow(0 4px 14px rgba(0, 0, 0, 0.35));
  }
  .sticker__title {
    font-family: "Montserrat", sans-serif;
    font-weight: 700;
    font-size: 58px;
    fill: var(--lime);
    letter-spacing: 1px;
  }
  .sticker__name {
    font-family: "Montserrat", sans-serif;
    font-weight: 700;
    font-size: 190px;
    fill: var(--text-white);
    letter-spacing: 4px;
  }
  .sticker__tagline {
    font-family: "Hind", sans-serif;
    font-weight: 600;
    font-size: 50px;
    fill: var(--text-white);
  }
  .sticker__url {
    font-family: "Hind", sans-serif;
    font-weight: 500;
    font-size: 34px;
    fill: var(--text-white);
  }
</style>
</head>
<body>
  <svg class="sticker" viewBox="0 0 1000 1000" role="img" aria-label="Clear Cable Record Format sticker: Built for open networks and open data, ccrf-sample.example">
    <defs>
      <clipPath id="face-clip">
        <circle cx="500" cy="500" r="466"/>
      </clipPath>
    </defs>

    <circle class="sticker__outer-ring" cx="500" cy="500" r="498" fill="var(--ring-blue)"/>
    <circle class="sticker__inner-ring" cx="500" cy="500" r="478" fill="var(--ring-white)"/>

    <g class="sticker__face" clip-path="url(#face-clip)">
      <rect x="0" y="0" width="1000" height="1000" fill="var(--night)"/>
      <ellipse class="sticker__top-cap" cx="500" cy="0" rx="185" ry="80" fill="var(--lime)"/>
      <ellipse class="sticker__base-band" cx="500" cy="1030" rx="580" ry="410" fill="var(--ring-blue)"/>
    </g>

    <circle class="sticker__hairline" cx="500" cy="500" r="446" fill="none" stroke="var(--lime)" stroke-width="3"/>

    <text class="sticker__title" x="500" y="160" text-anchor="middle">CLEAR CABLE</text>
    <text class="sticker__title" x="500" y="225" text-anchor="middle">RECORD FORMAT</text>

    <text class="sticker__name" x="500" y="530" text-anchor="middle">CCRF</text>

    <text class="sticker__tagline" x="500" y="722" text-anchor="middle">Built for open networks</text>
    <text class="sticker__tagline" x="500" y="776" text-anchor="middle">and open data</text>

    <rect class="sticker__url-pill" x="345" y="845" width="310" height="66" rx="33" fill="none" stroke="var(--lime)" stroke-width="4"/>
    <text class="sticker__url" x="500" y="889" text-anchor="middle">ccrf-sample.example</text>
  </svg>
</body>
</html>
```